Business Cards for company that supports physicians that do medical research

Need to create a business card for Qorvel Studies (www.qorvelstudies.example), a company devoted to supporting physicians who conduct medical research. The form of the card should match the message of research and information quest. I have provided the logo of the company as an uploaded file. Designs should be simple and slick aimed at very high end clients.

Target Market(s)

Medical doctors that are also researchers

Industry/Entity Type

Medical

Contact Information for Business Card

Should feature logo and fields for personal info:
Name/title
Phone /email

Font styles to use
Serif
Sans Serif

Requirements
Must have
• Qorvel logo and fields for personal info:
• Name: Bertrand Okonfu
• Title: VP Research and Senior Analyst
• Phone: 555-203-4719
• email: info@qorvelstudies.example
Nice to have
• Interesting cards that I've seen:
• 1- all black/charcoal or very dark background
• 2- Plastic - semi-transparent
• 3- non-standard height-width ratios
• 4- Functional cards -- USB drive incorporated
Should not have
• Too busy; needs to stay very simple

```html
<!DOCTYPE html>
<html lang="en">
<head>
<meta charset="utf-8">
<title>Qorvel Studies — Business Card</title>
<link rel="stylesheet" href="https://fonts.googleapis.com/css2?family=Source+Sans+3:ital,wght@0,400;0,600;0,700;1,400&display=swap">
<style>
  :root {
    --stage: #3b3b3b;
    --brand-blue: #1b7bbd;
    --brand-green: #45ab3f;
    --paper: #f6f6f6;
    --ink-light: #ffffff;
    --card-shadow: 0 3px 8px rgba(0,0,0,0.45);
  }
  * { margin: 0; padding: 0; box-sizing: border-box; }
  html, body { width: 1200px; height: 750px; overflow: hidden; }
  body {
    background: var(--stage);
    font-family: "Source Sans 3", "Myriad Pro", sans-serif;
    position: relative;
  }
  .card {
    position: absolute;
    top: 228px;
    width: 461px;
    height: 262px;
    box-shadow: var(--card-shadow);
    overflow: hidden;
  }
  .card--front { left: 124px; }
  .card--back { left: 618px; background: var(--brand-blue); }

  .card__art { position: absolute; inset: 0; }

  .contact {
    position: absolute;
    left: 20px;
    top: 82px;
    color: var(--ink-light);
  }
  .contact__name { font-size: 17px; font-weight: 600; line-height: 1; }
  .contact__title { font-size: 12.5px; font-weight: 400; margin-top: 5px; margin-left: 2px; }
  .contact__list { list-style: none; margin-top: 11px; margin-left: 2px; }
  .contact__item {
    display: flex; align-items: center; gap: 7px;
    font-size: 11.5px; height: 17.5px;
  }
  .contact__icon { width: 11px; height: 11px; flex: none; }

  .wordmark {
    position: absolute;
    font-weight: 700;
    letter-spacing: 0.2px;
    white-space: nowrap;
  }
  .card--front .wordmark {
    left: 265px; width: 180px; top: 112px;
    text-align: center; font-size: 27px;
    color: var(--brand-blue);
  }
  .card--back .wordmark {
    left: 0; right: 0; top: 102px;
    text-align: center; font-size: 34px;
    color: var(--ink-light);
  }
  .card__url {
    position: absolute; left: 0; right: 0; top: 217px;
    text-align: center;
    font-size: 11px; font-style: italic;
    letter-spacing: 2.6px;
    color: var(--ink-light);
  }
</style>
</head>
<body>

  <section class="card card--front" aria-label="Business card front">
    <svg class="card__art" viewBox="0 0 461 262" width="461" height="262" aria-hidden="true">
      <rect width="461" height="262" fill="var(--brand-blue)"/>
      <path d="M248 0 Q184 131 256 262 L461 262 L461 0 Z" fill="var(--paper)"/>
      <path d="M240 0 Q175 131 242 262 L256 262 Q184 131 248 0 Z" fill="var(--brand-green)"/>
    </svg>

    <div class="contact">
      <p class="contact__name">Bertrand Okonfu</p>
      <p class="contact__title">VP Research &amp; Senior Analyst</p>
      <ul class="contact__list">
        <li class="contact__item">
          <svg class="contact__icon" viewBox="0 0 12 12" aria-hidden="true"><path d="M2.4 0.6 L4.3 2.9 L3.3 4.3 Q4.4 6.9 7.7 8.7 L9.1 7.7 L11.4 9.6 L10 11.5 Q4.8 11.2 0.6 2.2 Z" fill="#fff"/></svg>
          <span>555-203-4719</span>
        </li>
        <li class="contact__item">
          <svg class="contact__icon" viewBox="0 0 12 12" aria-hidden="true"><rect x="0.5" y="2.5" width="11" height="7.5" fill="#fff"/><path d="M0.8 2.8 L6 6.8 L11.2 2.8" fill="none" stroke="var(--brand-blue)" stroke-width="1"/></svg>
          <span>info@qorvelstudies.example</span>
        </li>
        <li class="contact__item">
          <svg class="contact__icon" viewBox="0 0 12 12" aria-hidden="true"><circle cx="6" cy="6" r="5.5" fill="#fff"/><path d="M3.5 3 Q5.5 4 4.5 6 Q6.5 7 5.5 9.5 M7.5 2 Q8 4 9.5 4.5" fill="none" stroke="var(--brand-blue)" stroke-width="1.1"/></svg>
          <span>www.qorvelstudies.example</span>
        </li>
      </ul>
    </div>

    <p class="wordmark">Qorvel Studies</p>
  </section>

  <section class="card card--back" aria-label="Business card back">
    <p class="wordmark">Qorvel Studies</p>
    <p class="card__url">www.qorvelstudies.example</p>
  </section>

</body>
</html>
```